A clean crisp business card for a Landscape Construction company. Designed to be easy to read contact/ info and also be appealing/interesting, unlike a traditional business card.

Industry/Entity Type

Landscape Construction

Contact Information for Business Card

Company name : Brambleford Landscape Construction, phone number: (877) 62Vista, website:Bramblefordyards.example, Email, sales@bramblefordyards.example

Requirements
Nice to have
• Luxurious finishes/ details…. Icons or emblems next to contact info
Should not have
• Clipart or general pictures

```html
<!DOCTYPE html>
<html lang="en">
<head>
<meta charset="utf-8">
<title>Brambleford Landscape Construction – Business Card</title>
<link href="https://fonts.googleapis.com/css2?family=Cinzel:wght@500;600&family=Questrial&display=swap" rel="stylesheet">
<style>
  :root {
    --stage: #0b0b0c;
    --card: #121213;
    --edge-lime: #a6d62a;
    --brand-blue: #1f73c9;
    --brand-green: #8fc423;
    --text-light: #d6d6d6;
    --text-muted: #a9a9a9;
    --rule: #4a4a4a;
    --emboss: #2a2a2c;
  }
  html, body {
    margin: 0;
    width: 1200px;
    height: 820px;
    overflow: hidden;
    background: var(--stage);
  }
  .canvas {
    position: relative;
    width: 1200px;
    height: 820px;
  }
  .card {
    position: absolute;
    top: 250px;
    width: 540px;
    height: 310px;
    background: var(--card);
    box-sizing: border-box;
    border-left: 3px solid var(--edge-lime);
    border-bottom: 3px solid var(--edge-lime);
    box-shadow: 0 18px 40px rgba(0,0,0,0.7);
  }
  .card--front { left: 50px; }
  .card--back { left: 610px; }

  .brand-block {
    position: absolute;
    top: 48px;
    right: 40px;
    display: flex;
    align-items: center;
    gap: 10px;
  }
  .brand-dot {
    width: 14px;
    height: 14px;
    border-radius: 50%;
    background: var(--brand-green);
  }
  .brand-name {
    font-family: "Cinzel", serif;
    font-weight: 600;
    font-size: 17px;
    letter-spacing: 1px;
    color: var(--brand-green);
    line-height: 1.25;
    text-align: left;
  }
  .divider {
    position: absolute;
    left: 190px;
    right: 40px;
    top: 138px;
    height: 1px;
    background: var(--rule);
  }
  .person {
    position: absolute;
    left: 38px;
    top: 152px;
  }
  .person__name {
    font-family: "Cinzel", serif;
    font-weight: 600;
    font-size: 23px;
    letter-spacing: 0.5px;
    margin: 0;
  }
  .person__first { color: var(--brand-blue); }
  .person__last { color: var(--brand-green); }
  .person__title {
    font-family: "Questrial", sans-serif;
    font-size: 15px;
    color: var(--text-light);
    margin: 4px 0 0 2px;
  }
  .contact {
    position: absolute;
    right: 36px;
    top: 156px;
    font-family: "Questrial", sans-serif;
    font-size: 13.5px;
    color: var(--text-light);
    text-align: right;
    line-height: 1.45;
  }
  .contact__address { margin: 0 18px 8px 0; }
  .contact__row {
    display: flex;
    justify-content: flex-end;
    align-items: center;
    gap: 7px;
  }
  .contact__icon { width: 11px; height: 11px; flex: none; }

  .back-mark {
    position: absolute;
    inset: 0;
    display: flex;
    align-items: center;
    justify-content: center;
    gap: 14px;
  }
  .back-mark__dot {
    width: 34px;
    height: 34px;
    border-radius: 50%;
    background: var(--emboss);
  }
  .back-mark__name {
    font-family: "Cinzel", serif;
    font-weight: 600;
    font-size: 34px;
    letter-spacing: 2px;
    color: var(--emboss);
  }
</style>
</head>
<body>
<main class="canvas">

  <section class="card card--front" aria-label="Business card front">
    <div class="brand-block">
      <span class="brand-dot"></span>
      <div class="brand-name">Brambleford<br>Landscape Construction</div>
    </div>

    <div class="divider"></div>

    <div class="person">
      <h1 class="person__name"><span class="person__first">Daniel</span> <span class="person__last">Hartley</span></h1>
      <p class="person__title">Managing Director</p>
    </div>

    <address class="contact">
      <p class="contact__address">421, Address line Address<br>here 45452, Country Name</p>
      <div class="contact__row">(877) 62Vista
        <svg class="contact__icon" viewBox="0 0 12 12"><path d="M2.5 1 L4.5 1 L5.3 3.6 L4 4.6 Q5 7 7.4 8 L8.4 6.7 L11 7.5 L11 9.5 Q10.5 11 9 11 Q1 10 1 3 Q1 1.5 2.5 1 Z" fill="var(--brand-green)"/></svg>
      </div>
      <div class="contact__row">sales@bramblefordyards.example
        <svg class="contact__icon" viewBox="0 0 12 12"><rect x="0.5" y="2.5" width="11" height="7.5" fill="var(--brand-green)"/><path d="M0.8 2.8 L6 7 L11.2 2.8" stroke="var(--card)" stroke-width="1" fill="none"/></svg>
      </div>
      <div class="contact__row">www.Bramblefordyards.example
        <svg class="contact__icon" viewBox="0 0 12 12"><circle cx="6" cy="6" r="5.3" fill="var(--brand-green)"/><g stroke="var(--card)" stroke-width="0.8" fill="none"><ellipse cx="6" cy="6" rx="2.3" ry="5.3"/><path d="M0.7 6 H11.3 M1.5 3.4 H10.5 M1.5 8.6 H10.5"/></g></svg>
      </div>
    </address>
  </section>

  <section class="card card--back" aria-label="Business card back">
    <div class="back-mark">
      <span class="back-mark__dot"></span>
      <span class="back-mark__name">Brambleford</span>
    </div>
  </section>

</main>
</body>
</html>
```